Business cards in digital learning for freelancer

Hello, I need a business cards in french. I work in the Digital learning industries as freeelancer; I'm an expert in digital learning. I work in France. My customer are in the health industry, pharmaceutical industry, and training organization. I've got a logo. I offer three services: consulting, Design, and Training. In the consulting, I offers coaching to choose your digital learning tools and the digital learning strategy. For the Design, I product differents level of elearning like rapid-learning, elearning, micro-learning, video-learning. And for the training service, I've create training about pedagogy, digital learning management project, Digital learning design.
I join my Logo create in this platform. My universe is gamified. I like the life, and I'm very social. I want a card like I'm I. I love Art (painting), Europeen comics. I use in my visual support "permanent maker" font and caracters. I would like cards: elegant, modern, Top class. If you need any information, you can ask me.
thanks for ideas

Target Market(s)

in health industries and training organization for Training manager, instructor, human resources director

Contact Information for Business Card

Phone number : 06 71 38 95 14 , mail: bastiengolmier@quelmoto.fr, web: bastiengolmier.fr , Carrivo

Font styles to use
Sans Serif

Requirements
Must have
• Use my logo and write my 3 services (consulting, training, design)

```html
<!DOCTYPE html>
<html lang="fr">
<head>
<meta charset="utf-8">
<title>Golmier Digital Learning – cartes de visite</title>
<link href="https://fonts.googleapis.com/css2?family=Arimo:wght@400;700&family=Marcellus&display=swap" rel="stylesheet">
<style>
  :root {
    --orange: #ee7326;
    --grey: #6f6f6f;
    --grey-light: #9a9a9a;
    --paper: #f7f7f6;
    --backdrop: #dcdcdc;
    --white: #ffffff;
    --social: #1a73b8;
  }
  * { margin: 0; padding: 0; box-sizing: border-box; }
  html, body { width: 1200px; height: 930px; overflow: hidden; }
  body {
    background: var(--backdrop);
    position: relative;
    font-family: "Arimo", Arial, sans-serif;
  }
  .card {
    position: absolute;
    width: 560px;
    height: 340px;
    box-shadow: 0 14px 30px rgba(0,0,0,0.15);
  }
  .card--front { left: 60px; top: 490px; background: var(--paper); }
  .card--back { left: 580px; top: 100px; background: var(--orange); }

  .brand { position: absolute; text-align: center; }
  .brand__row { display: flex; align-items: center; justify-content: center; gap: 12px; }
  .brand__dot { width: 30px; height: 30px; border-radius: 50%; }
  .brand__name {
    font-family: "Arimo", Arial, sans-serif;
    font-weight: 700;
    font-size: 40px;
    letter-spacing: 3px;
    line-height: 1;
  }
  .brand__tagline {
    font-family: "Marcellus", serif;
    font-size: 12px;
    letter-spacing: 3px;
    text-transform: uppercase;
    margin-top: 8px;
    display: flex; align-items: center; gap: 8px; justify-content: center;
  }
  .brand__tagline::before, .brand__tagline::after {
    content: ""; height: 1px; width: 34px; background: currentColor;
  }

  .card--front .brand { left: 250px; top: 80px; width: 280px; }
  .card--front .brand__dot { background: var(--orange); }
  .card--front .brand__name { color: var(--orange); }
  .card--front .brand__tagline { color: var(--grey); }

  .card--back .brand { left: 0; top: 110px; width: 560px; }
  .card--back .brand__dot { background: var(--white); }
  .card--back .brand__name { color: var(--white); font-size: 48px; }
  .card--back .brand__tagline { color: var(--white); font-size: 13px; }
  .services {
    margin-top: 16px;
    color: var(--white);
    font-family: "Marcellus", serif;
    font-size: 13px;
    letter-spacing: 2px;
    text-transform: uppercase;
  }
  .services span + span::before { content: "●"; margin: 0 8px; font-size: 9px; vertical-align: 2px; }

  .person { position: absolute; left: 34px; top: 60px; }
  .person__name {
    font-family: "Marcellus", serif;
    color: var(--orange);
    font-size: 20px;
    font-variant: small-caps;
    letter-spacing: 1.5px;
  }
  .person__role { color: var(--grey); font-size: 13px; margin-top: 2px; }
  .contact { list-style: none; margin-top: 12px; color: var(--grey); font-size: 13px; }
  .contact li { display: flex; align-items: center; gap: 8px; margin-bottom: 6px; }
  .contact svg { width: 13px; height: 13px; flex: none; }

  .divider { position: absolute; left: 34px; right: 80px; top: 232px; height: 1px; background: var(--grey-light); }

  .web { position: absolute; right: 80px; top: 250px; font-size: 14px; color: var(--grey); }
  .web__domain { color: var(--orange); }
  .social { position: absolute; right: 30px; top: 242px; display: flex; flex-direction: column; align-items: center; gap: 3px; }
  .social__dot { width: 26px; height: 26px; border-radius: 50%; background: var(--social); }
  .social__name { font-size: 10px; color: var(--grey); }
</style>
</head>
<body>
  <section class="card card--back" aria-label="Verso de la carte">
    <div class="brand">
      <div class="brand__row">
        <span class="brand__dot"></span>
        <span class="brand__name">GOLMIER</span>
      </div>
      <div class="brand__tagline">Digital Learning</div>
      <div class="services"><span>Consulting</span><span>Training</span><span>Design</span></div>
    </div>
  </section>

  <section class="card card--front" aria-label="Recto de la carte">
    <div class="person">
      <div class="person__name">Bastien Golmier</div>
      <div class="person__role">Managing Director</div>
      <ul class="contact">
        <li>
          <svg viewBox="0 0 16 16" aria-hidden="true"><path fill="var(--orange)" d="M4 1.5l2.2 3-1.3 1.6c.9 1.9 2.4 3.4 4.3 4.3l1.6-1.3 3 2.2-1.2 2.4C7.300 13.2 2.800 8.700 1.600 2.700z"/></svg>
          06 71 38 95 14
        </li>
        <li>
          <svg viewBox="0 0 16 16" aria-hidden="true"><rect x="1" y="3" width="14" height="10" fill="var(--orange)"/><path d="M1 3l7 6 7-6" fill="none" stroke="var(--white)" stroke-width="1.3"/></svg>
          bastiengolmier@quelmoto.fr
        </li>
      </ul>
    </div>

    <div class="brand">
      <div class="brand__row">
        <span class="brand__dot"></span>
        <span class="brand__name">GOLMIER</span>
      </div>
      <div class="brand__tagline">Digital Learning</div>
    </div>

    <div class="divider"></div>
    <div class="web">www.<span class="web__domain">bastiengolmier.fr</span></div>
    <div class="social">
      <span class="social__dot"></span>
      <span class="social__name">Carrivo</span>
    </div>
  </section>
</body>
</html>
```